Complete redesign of Licensed Medical Cannabis Dispensary website

Redesign website to modernize it and simplify it and add a self service reservation/preorder interactive delivery form. Also integrate current POS system that has current inventory. Here is a website for inspiration that I really like because of it simplicity https://www.leafroute.example and easy ordering option. Attached is our logo.... please design around that and this is our website address www.meadowcrestcourier.example

Font styles to use
Sans Serif

Colors
5c5c5c
cbcbcb
000000
add136

Requirements
Must have
• inventory thats integrated with pos
• online reservation/delivery form
Nice to have
• a website thats modern and simple
• The website designed are the logo that is attached
Should not have
• too much information

```html
<!DOCTYPE html>
<html lang="en">
<head>
<meta charset="utf-8">
<title>Meadowcrest Courier – Medical Delivery</title>
<link href="https://fonts.googleapis.com/css2?family=Open+Sans:wght@400;600;700&display=swap" rel="stylesheet">
<style>
:root{
  --lime:#a3cc2e;
  --green:#26801c;
  --ink:#000000;
  --text:#333333;
  --grey:#5c5c5c;
  --line:#cbcbcb;
  --pale:#f2f2f2;
  --hero:#e6e6e6;
  --dark:#333333;
  --white:#ffffff;
}
*{box-sizing:border-box;margin:0;padding:0}
html,body{width:1200px;height:2740px;overflow:hidden}
body{font-family:"Open Sans",Arial,sans-serif;color:var(--text);background:var(--white)}
.wrap{width:936px;margin:0 auto;position:relative}
.btn{display:inline-block;font-weight:600;font-size:17px;padding:0 18px;height:45px;line-height:45px;border-radius:2px;color:var(--ink);background:var(--lime)}
.btn.dark{background:var(--dark);color:var(--white)}

/* header */
.site-header{height:100px;background:var(--pale)}
.site-header .wrap{height:100px}
.brand{position:absolute;left:4px;top:26px;display:flex;align-items:center;gap:10px;font-size:20px;font-weight:600;color:var(--green)}
.brand-dot{width:40px;height:40px;border-radius:50%;background:var(--green)}
.orders{position:absolute;right:114px;top:24px;font-size:17px;color:var(--grey);display:flex;align-items:center;gap:6px}
.round-btn{position:absolute;top:17px;width:40px;height:40px;border-radius:50%;background:var(--green);display:flex;align-items:center;justify-content:center}
.round-btn.search{right:62px}
.round-btn.cart{right:0}
.cart-count{position:absolute;left:-2px;top:-2px;width:15px;height:15px;border-radius:50%;background:var(--dark);color:var(--white);font-size:9px;text-align:center;line-height:15px}
.main-nav{position:absolute;right:0;top:68px;display:flex;gap:26px;font-size:12px;color:var(--text)}
.main-nav .current{color:var(--green)}

/* hero */
.hero{height:516px;background:var(--hero);position:relative}
.hero .wrap{height:516px}
.hero h1{position:absolute;left:0;top:140px;font-size:52px;line-height:58px;font-weight:600;color:var(--green)}
.hero p{position:absolute;left:0;top:273px;font-size:18px;color:var(--grey)}
.hero .actions{position:absolute;left:0;top:316px;display:flex;gap:10px}
.hero-visual{position:absolute;left:590px;top:28px;width:346px;height:480px;border-radius:6px;background:radial-gradient(ellipse at 50% 75%,#6f7f3a 0%,#a7a883 45%,#e6e6e6 75%),linear-gradient(#e39a2a,#e6e6e6)}
.arrow{position:absolute;top:50%;transform:translateY(-50%)}
.arrow.prev{left:46px}
.arrow.next{right:46px}

/* reservation */
.reservation{height:118px;background:var(--lime)}
.reservation h2{text-align:center;color:var(--white);font-size:24px;font-weight:700;padding-top:18px;letter-spacing:.5px}
.res-form{display:flex;gap:12px;margin-top:12px}
.res-field{width:165px;height:33px;background:var(--white);font-size:11px;color:var(--grey);padding:0 14px;line-height:33px;position:relative}
.res-field.select::after{content:"";position:absolute;right:12px;top:14px;border:5px solid transparent;border-top-color:var(--grey)}
.res-submit{width:51px;height:33px;background:var(--ink);color:var(--white);font-size:9px;font-weight:600;text-align:center;line-height:33px}

/* steps */
.steps{height:363px;border-bottom:2px solid var(--line)}
.steps .wrap{display:flex;justify-content:space-between;padding-top:80px}
.step{width:290px;text-align:center}
.step-icon{width:133px;height:133px;border-radius:50%;background:var(--lime);margin:0 auto;display:flex;align-items:center;justify-content:center}
.step h3{font-size:25px;font-weight:700;color:var(--green);margin-top:10px;letter-spacing:.5px}
.step p{font-size:11.5px;line-height:17px;color:var(--text)}

/* products */
.products{height:721px}
.section-title{text-align:center;font-size:24px;font-weight:700;color:var(--green);letter-spacing:.5px}
.products .section-title{padding-top:78px}
.product-grid{display:grid;grid-template-columns:repeat(4,190px);column-gap:58px;row-gap:42px;margin-top:30px}
.product{text-align:center}
.product-photo{height:150px;background:radial-gradient(circle at 40% 40%,#9aa85a,#5c6a2c 60%,#2f3618)}
.product-name{font-size:13px;margin-top:12px;color:var(--ink)}
.product-price{font-size:13px;color:var(--ink)}
.view-all{text-align:center;margin-top:28px}

/* testimonials */
.testimonials{height:360px;background:var(--pale);position:relative;text-align:center}
.testimonials .section-title{padding-top:76px}
.quote{font-size:23px;color:var(--ink);margin-top:22px}
.author{font-size:15px;color:var(--ink);margin-top:12px}
.avatar{width:76px;height:76px;border-radius:50%;background:linear-gradient(135deg,#c58a6a,#5a2c2a);margin:16px auto 0}

/* calls to action */
.cta{height:274px}
.cta .wrap{display:flex;justify-content:space-between;padding-top:36px}
.cta-box{width:452px;height:206px;border:2px solid var(--line);text-align:center;padding-top:26px}
.cta-box h3{font-size:24px;line-height:32px;font-weight:700;color:var(--green);margin:0 auto 18px;width:380px}

/* footer */
.site-footer{height:288px;background:var(--pale)}
.footer-cols{position:relative;height:220px;border-bottom:1px solid var(--line)}
.footer-col{position:absolute;top:52px}
.footer-col h4{font-size:16px;font-weight:600;color:var(--ink);margin-bottom:12px}
.footer-col li{list-style:none;font-size:11px;line-height:20px;color:var(--grey)}
.social{display:flex;gap:8px}
.social span{width:27px;height:27px;border-radius:50%;background:#3b5a9a}
.social span+span{background:#2aa3e0}
.copyright{text-align:center;font-size:11px;color:var(--grey);padding-top:24px}
</style>
</head>
<body>

<header class="site-header">
  <div class="wrap">
    <div class="brand"><span class="brand-dot"></span>Meadowcrest Courier</div>
    <div class="orders">
      <svg width="14" height="14" viewBox="0 0 24 24"><path fill="#5c5c5c" d="M6.6 10.8a15 15 0 006.6 6.6l2.2-2.2c.3-.3.7-.4 1-.2 1.1.4 2.3.6 3.6.6.6 0 1 .4 1 1V20c0 .6-.4 1-1 1A17 17 0 013 4c0-.6.4-1 1-1h3.5c.6 0 1 .4 1 1 0 1.3.2 2.5.6 3.6.1.3 0 .7-.2 1z"/></svg>
      Orders : 555-014-2290
    </div>
    <div class="round-btn search"><svg width="16" height="16" viewBox="0 0 24 24"><circle cx="10" cy="10" r="6.5" fill="none" stroke="#fff" stroke-width="3"/><path d="M15 15l6 6" stroke="#fff" stroke-width="3.5" stroke-linecap="round"/></svg></div>
    <div class="round-btn cart"><span class="cart-count">0</span><svg width="16" height="16" viewBox="0 0 24 24"><path fill="#fff" d="M2 3h4l1 3h15l-3 8H8.5L8 16h12v2H6l1.5-4L5 5H2z"/><circle cx="8" cy="20.5" r="1.7" fill="#fff"/><circle cx="18" cy="20.5" r="1.7" fill="#fff"/></svg></div>
    <nav class="main-nav">
      <span class="current">Home</span><span>About Us</span><span>Services</span><span>Forums</span><span>Contact</span><span>Log In / Sign Up</span>
    </nav>
  </div>
</header>

<section class="hero">
  <svg class="arrow prev" width="14" height="26" viewBox="0 0 14 26"><path d="M12 2L2 13l10 11" fill="none" stroke="#5c5c5c" stroke-width="2.5"/></svg>
  <div class="wrap">
    <h1>Top Shelf Medical<br>Marijuana Delivery</h1>
    <p>We offer only the highest quality flowers, edibles and concentrates.</p>
    <div class="actions"><span class="btn">Shop Now</span><span class="btn dark">Get Verified</span></div>
    <div class="hero-visual" role="img" aria-label="Prescription bottle with cannabis buds"></div>
  </div>
  <svg class="arrow next" width="14" height="26" viewBox="0 0 14 26"><path d="M2 2l10 11L2 24" fill="none" stroke="#5c5c5c" stroke-width="2.5"/></svg>
</section>

<section class="reservation">
  <div class="wrap">
    <h2>ONLINE RESERVATION</h2>
    <div class="res-form">
      <div class="res-field">Name</div>
      <div class="res-field">Email</div>
      <div class="res-field">Phone</div>
      <div class="res-field">Address</div>
      <div class="res-field select">Medicine Type</div>
      <div class="res-submit">SUBMIT</div>
    </div>
  </div>
</section>

<section class="steps">
  <div class="wrap">
    <div class="step">
      <div class="step-icon"><svg width="56" height="64" viewBox="0 0 56 64" fill="none" stroke="#111" stroke-width="2.5"><path d="M6 4h34l10 10v46H6z"/><path d="M40 4v10h10"/><rect x="14" y="22" width="10" height="10"/><path d="M30 24h12M30 30h12M14 40h28M14 46h28M14 52h20"/></svg></div>
      <h3>GET VERIFIED</h3>
      <p>It's fast. It's simple. Just fill out our verification form and get approved in minutes.</p>
    </div>
    <div class="step">
      <div class="step-icon"><svg width="66" height="56" viewBox="0 0 66 56" fill="none" stroke="#111" stroke-width="2.5"><path d="M20 20L33 4l13 16"/><rect x="4" y="20" width="58" height="9" rx="2"/><path d="M8 29l5 23h40l5-23"/><rect x="20" y="34" width="5" height="13"/><rect x="30.5" y="34" width="5" height="13"/><rect x="41" y="34" width="5" height="13"/></svg></div>
      <h3>SHOP</h3>
      <p>Add the products you want to your shopping cart and check out. No credit card required!</p>
    </div>
    <div class="step">
      <div class="step-icon"><svg width="60" height="60" viewBox="0 0 60 60" fill="none" stroke="#111" stroke-width="2.5"><path d="M30 4L54 16v28L30 56 6 44V16z"/><path d="M6 16l24 12 24-12M30 28v28M18 10l24 12v10"/><path d="M36 46l6-3"/></svg></div>
      <h3>GET MEDICATED</h3>
      <p>Sit back and wait. Our professional staff will deliver your medication right to your front door.</p>
    </div>
  </div>
</section>

<section class="products">
  <div class="wrap">
    <h2 class="section-title">FLOWERS</h2>
    <div class="product-grid">
      <div class="product"><div class="product-photo" role="img" aria-label="Close-up of cannabis flower"></div><div class="product-name">Scout Crumble</div><div class="product-price">$25.00</div></div>
      <div class="product"><div class="product-photo" role="img" aria-label="Close-up of cannabis flower"></div><div class="product-name">Sticky Mint</div><div class="product-price">$30.00</div></div>
      <div class="product"><div class="product-photo" role="img" aria-label="Close-up of cannabis flower"></div><div class="product-name">Dusk Sorbet</div><div class="product-price">$15.00 - $60.00</div></div>
      <div class="product"><div class="product-photo" role="img" aria-label="Close-up of purple cannabis flower"></div><div class="product-name">Blue Crumble</div><div class="product-price">$25.00 - $60.00</div></div>
      <div class="product"><div class="product-photo" role="img" aria-label="Cannabis flower in a container"></div><div class="product-name">Ridge Resin #4</div><div class="product-price">$15.00 - $60.00</div></div>
      <div class="product"><div class="product-photo" role="img" aria-label="Pre-rolled joint on flower"></div><div class="product-name">Preroll</div><div class="product-price">$30.00</div></div>
      <div class="product"><div class="product-photo" role="img" aria-label="Close-up of cannabis flower"></div><div class="product-name">Halo Band OZ</div><div class="product-price">$15.00 - $75.00</div></div>
      <div class="product"><div class="product-photo" role="img" aria-label="Close-up of cannabis flower"></div><div class="product-name">Sugar Valley</div><div class="product-price">$15.00 - $30.00</div></div>
    </div>
    <div class="view-all"><span class="btn dark">View All</span></div>
  </div>
</section>

<section class="testimonials">
  <svg class="arrow prev" width="14" height="26" viewBox="0 0 14 26"><path d="M12 2L2 13l10 11" fill="none" stroke="#5c5c5c" stroke-width="2.5"/></svg>
  <h2 class="section-title">TESTIMONIALS</h2>
  <p class="quote">“This dispensary has the very best med! I love their sour tangerine!”</p>
  <p class="author">MARA T.</p>
  <div class="avatar" role="img" aria-label="Customer portrait"></div>
  <svg class="arrow next" width="14" height="26" viewBox="0 0 14 26"><path d="M2 2l10 11L2 24" fill="none" stroke="#5c5c5c" stroke-width="2.5"/></svg>
</section>

<section class="cta">
  <div class="wrap">
    <div class="cta-box">
      <h3>DON’T HAVE YOUR DOCTOR’S RECOMMENDATION YET? GET IT ONLINE FOR JUST $49!</h3>
      <span class="btn">Get Started</span>
    </div>
    <div class="cta-box">
      <h3>STILL NOT A MEMBER OF OUR DISPENSARY?</h3>
      <span class="btn">Get Verified</span>
    </div>
  </div>
</section>

<footer class="site-footer">
  <div class="wrap">
    <div class="footer-cols">
      <div class="footer-col" style="left:0"><h4>EXPLORE</h4><ul><li>Store</li><li>Cart</li><li>My Account</li><li>New Patient Verification</li><li>Contact Us</li></ul></div>
      <div class="footer-col" style="left:248px"><h4>FORUMS</h4><ul><li>Bongs, Bubblers, &amp; Water Pipes</li><li>Concentrates</li><li>Growing</li><li>Vaporizers</li><li>What Are You Smokin'?</li></ul></div>
      <div class="footer-col" style="left:544px"><h4>RECENT TOPICS</h4><ul><li>Glass or metal?</li><li>Sexing your plant</li></ul></div>
      <div class="footer-col" style="left:816px"><h4>FOLLOW US ON</h4><div class="social"><span></span><span></span></div></div>
    </div>
    <p class="copyright">Copyright © 2018 Meadowcrest Courier. All rights reserved.</p>
  </div>
</footer>

</body>
</html>
```